professional business card design

Business card design. Photos have been uploaded and i am open to the designer choosing which photos to use. Would like the card to be mostyly in a grey scale design with black, whites, silver & grey colours. I have added copy of our flyer as would like on the back side of card our services to be listed. Do not use any bright colurs such as blue red green or yellow. i need to be able to edit the phone number and naem in the final card design submitted.

Target Market(s)

Clients

Industry/Entity Type

earhmovibng and transport

Contact Information for Business Card

Director Name, address, email, phone number and services

Colors

Designer to choose only greyscale colors for use in the design.

Requirements
Should not have
• no yellow, red, blue or green

```html
<!DOCTYPE html>
<html lang="en">
<head>
<meta charset="utf-8">
<title>Business Card – Front and Back</title>
<link rel="stylesheet" href="https://fonts.googleapis.com/css2?family=Montserrat:wght@400;500;700&display=swap">
<style>
  :root {
    --page-bg: #e8e6e3;
    --card-bg: #ffffff;
    --accent: #7d7d7d;
    --accent-strong: #4a4a4a;
    --ink: #222222;
    --truck-dark: #3a3a3a;
    --truck-mid: #8a8886;
    --truck-light: #c9c8c6;
  }
  * { margin: 0; padding: 0; box-sizing: border-box; }
  html, body {
    width: 1200px; height: 848px; overflow: hidden;
    background: var(--page-bg);
    font-family: "Montserrat", sans-serif;
    color: var(--ink);
  }
  .card {
    position: absolute; left: 289px; width: 600px; height: 327px;
    background: var(--card-bg);
    box-shadow: 0 3px 10px rgba(0,0,0,0.18);
  }
  .card--front { top: 76px; }
  .card--back { top: 443px; }

  .truck-photo {
    position: absolute; border-radius: 6px;
    background: linear-gradient(100deg, var(--truck-mid) 0%, var(--truck-light) 35%, var(--truck-dark) 70%, var(--truck-mid) 100%);
  }
  .card--front .truck-photo { left: 45px; top: 85px; width: 285px; height: 158px; }

  .divider {
    position: absolute; left: 342px; top: 74px; width: 2px; height: 180px;
    background: var(--accent);
  }
  .contact-block { position: absolute; left: 357px; top: 70px; }
  .contact-block__name {
    font-weight: 700; font-size: 24px; color: var(--accent-strong);
    letter-spacing: 0.3px; line-height: 1;
  }
  .contact-block__title { font-size: 15px; margin-top: 7px; }
  .contact-list { list-style: none; margin-top: 19px; }
  .contact-list li {
    display: flex; align-items: center; gap: 6px;
    font-size: 15px; height: 21.5px;
  }
  .contact-list svg { width: 13px; height: 13px; flex: none; }
  .contact-block__address { font-size: 15px; line-height: 22px; margin-top: 13px; }
  .tagline {
    position: absolute; left: 0; right: 0; top: 268px;
    text-align: center; font-size: 14.5px; line-height: 21px;
  }

  .card--back .truck-photo--pair { left: 22px; top: 18px; width: 226px; height: 114px; }
  .card--back .truck-photo--tanker { left: 282px; top: 18px; width: 298px; height: 106px; }

  .services-heading {
    position: absolute; left: 189px; top: 140px; width: 221px; height: 32px;
    border: 2px solid var(--accent); border-radius: 16px;
    background: var(--card-bg);
    display: flex; align-items: center; justify-content: center;
    font-size: 22px; font-weight: 500; letter-spacing: 0.8px;
  }
  .services-list {
    position: absolute; list-style: none; top: 179px;
  }
  .services-list--left { left: 22px; }
  .services-list--right { left: 376px; top: 181px; }
  .services-list li {
    position: relative; padding-left: 19px;
    font-size: 15px; height: 21.5px; line-height: 21.5px;
  }
  .services-list li::before {
    content: ""; position: absolute; left: 0; top: 6px;
    width: 10px; height: 10px; border-radius: 50%;
    background: var(--accent);
  }
</style>
</head>
<body>

<section class="card card--front">
  <div class="truck-photo" role="img" aria-label="Photo of two prime mover trucks, silver and black"></div>
  <div class="divider"></div>
  <div class="contact-block">
    <h1 class="contact-block__name">DANIEL HARTLEY</h1>
    <p class="contact-block__title">Managing Director</p>
    <ul class="contact-list">
      <li>
        <svg viewBox="0 0 16 16" aria-hidden="true"><path fill="#7d7d7d" d="M1 5c0-2 3-3 7-3s7 1 7 3v1.5h-3.5V5h-7v1.5H1zM3 8l2-2h6l2 2v5H3z"/><circle cx="8" cy="10" r="1.6" fill="#fff"/></svg>
        120 555 014
      </li>
      <li>
        <svg viewBox="0 0 16 16" aria-hidden="true"><rect x="1" y="3" width="14" height="10" fill="#7d7d7d"/><path d="M1 3l7 6 7-6" fill="none" stroke="#fff" stroke-width="1.3"/></svg>
        info@ridgelinehaul.com
      </li>
      <li>
        <svg viewBox="0 0 16 16" aria-hidden="true"><circle cx="8" cy="8" r="7" fill="#7d7d7d"/><path d="M1.5 8h13M8 1c-3 3-3 11 0 14M8 1c3 3 3 11 0 14" fill="none" stroke="#fff" stroke-width="1"/></svg>
        www.ridgelinehaul.com
      </li>
    </ul>
    <p class="contact-block__address">Depot: Lot 41 Redgum Flat<br>Road Ironbark</p>
  </div>
  <p class="tagline">We offer a large range of services not listed so<br>Call us today for a personalised quote to suit your needs.</p>
</section>

<section class="card card--back">
  <div class="truck-photo truck-photo--pair" role="img" aria-label="Photo of two prime mover trucks, silver and black"></div>
  <div class="truck-photo truck-photo--tanker" role="img" aria-label="Photo of a black road train towing silver tanker trailers"></div>
  <h2 class="services-heading">OUR SERVICES</h2>
  <ul class="services-list services-list--left">
    <li>Over Size Loads / Hot Shot Loads</li>
    <li>Heavy Vehicle Recovery Services</li>
    <li>Potable Water Deliveries</li>
    <li>Road Building / Maintenance</li>
    <li>Earthworks</li>
    <li>Sand &amp; Mental Supply &amp; Cartage</li>
  </ul>
  <ul class="services-list services-list--right">
    <li>Road Train Tippers</li>
    <li>Road Train Tankers</li>
    <li>Road Rrain Flat Tops</li>
    <li>Drop Deck Trailers</li>
    <li>Mine Site accredited</li>
    <li>equipment &amp; Operattors</li>
  </ul>
</section>

</body>
</html>
```